San Francisco Leading Consulting firm - 47Vora Web Design Project

•Create a Web Design
•Uncoded webpage layout design
•2 Pages Design - Homepage + Interior Page

Task Description
Hello, we're looking for a re-design our current website www.47vora-example.com

we have a sample mockup design @

http://47vora.pubtrellis-example.org/

This shows the layout that we like and also a sample of 6 pictures that would change based on where you mouse over..

6 pictures HOME design needs to be included.

SMART
THOUGHTFUL
FLEXIBLE
CREATIVE SERVICES
TECHNICAL SERVICES
PARTNERS

sites we like:

http://www.melvanadvisory-example.com/Home.cfm?id=Home
http://www.plinthworks-example.com/index.html

Our company can be best described as: 100+ employees, cutting-edge, depandable, innovative, strong, smart.

Our Primary focus is: IT Consulting Services and Creative Design services

47Vora LLC is a consulting firm providing creative design, business and technology solutions to both private and public interests.

Established in 1996, 47Vora is a San Francisco based company providing specialists for a range of business needs including:

Creative Design Services
•Print
•Logo Design
•Website Design
•Illustration

and

Business and Technology solutions

•Application Software and Web Development
•Business Process Re-Design (BPR)
•Business/Systems Analysis and Requirement Documentation
•Mentoring and Training
•Network/Hardware Installation Services
•System Design and Architecture
•Vendor Management
•Docuvault Architecture and Implementation

our sample mockup site:

Reason: Due to holiday season, we're not available to work with designers and finilize our design.  

Thank you very much for submitting your design.

We appreciate your time and creativity.   Since, our office is currently closed for holidays, we will be reviewing it in details next week and will make our decision as soon as possible.

It would be great if you could submit any of your changes by Wed next week, so it would be part of our reviews. 

Please see updated wireframe under attachments:  we have some minor updates to our wireframe that we would like you to update your designs, if possible.  

We also encorouge you not to use our standard wireframe and come up with more unique designs.   Everything would be considered when we review your design.

 

Ardenne Market(s)

Creative services and professional services clients, including government agencies

Industry/Entity Type

Business

Requirements
Must have
• Clean, professional look, easy navigation

```html
<!DOCTYPE html>
<html lang="en">
<head>
<meta charset="utf-8">
<title>47Vora — Consulting, Creative and Technical Services</title>
<link href="https://fonts.googleapis.com/css2?family=Arimo:wght@400;700&family=PT+Sans+Narrow&display=swap" rel="stylesheet">
<style>
:root{
  --blue:#0a8cc6;
  --blue-dark:#0676ac;
  --text:#222;
  --muted:#6a6a6a;
  --nav:#555;
  --rule:#c9c9c9;
  --slide-green:#b7d35a;
  --slide-deep:#5f8d1e;
  --white:#fff;
}
*{box-sizing:border-box;margin:0;padding:0}
html,body{width:1200px;height:1100px;overflow:hidden;background:var(--white)}
body{position:relative;font-family:"Arimo",Helvetica,Arial,sans-serif;color:var(--text)}
.abs{position:absolute}

.brand{left:135px;top:28px;display:flex;align-items:center;gap:10px;font-size:27px;letter-spacing:2px;color:#3d4a55}
.brand-dot{width:26px;height:26px;border-radius:50%;background:var(--blue)}

.main-nav{left:346px;top:40px;display:flex;font-size:14.5px;color:var(--nav);letter-spacing:.3px}
.main-nav span{padding:0 12px;border-left:1px solid var(--blue);line-height:18px}
.main-nav span:first-child{border-left:none;padding-left:8px}

.contact{left:929px;top:12px;font-size:11.5px;line-height:18px;color:var(--text)}
.contact .link{color:var(--blue);font-weight:700}

.hero{left:0;top:93px;width:1200px;height:487px;background:linear-gradient(180deg,#e9e9e9 0%,#cfcfcf 40%,#8e8e8e 75%,#6f6f6f 100%)}
.slide-tab{top:175px;width:21px;height:285px;background:rgba(190,220,110,.55)}
.slide{left:139px;top:131px;width:920px;height:399px;border-radius:8px;background:var(--white);overflow:hidden}
.slide-photo{position:absolute;left:0;top:0;width:920px;height:352px;background:linear-gradient(180deg,#eef0c9 0%,#c9dc6a 30%,var(--slide-green) 55%,#e7c7b6 80%,#f2dedc 100%)}
.slide-title{left:81px;top:126px;font-size:48px;font-weight:700;color:#111;letter-spacing:-.5px}
.slide-sub{left:84px;top:172px;font-family:"PT Sans Narrow","Arial Narrow",sans-serif;font-size:24px;line-height:24px;color:var(--slide-deep)}
.dots{left:383px;top:370px;display:flex;gap:14px}
.dots i{width:14px;height:14px;border-radius:50%;background:#111}
.dots i.on{background:var(--blue)}
.arrow{top:280px}

.card{top:602px;width:300px;height:130px;border:1px solid var(--blue);border-radius:3px;overflow:hidden;background:var(--white)}
.card-head{height:26px;background:linear-gradient(180deg,#1b9ed6,var(--blue-dark));color:var(--white);font-weight:700;font-size:15px;padding:4px 16px}
.card-art{position:absolute;left:30px;top:28px;width:240px;height:102px}
.card-corner{position:absolute;right:0;bottom:0}

.rule{left:122px;width:960px;height:1px;background:var(--rule)}

.featured{left:124px;top:770px;font-size:18px;font-weight:700;line-height:20px;color:var(--text)}
.clients{left:260px;top:780px;width:820px;display:flex;justify-content:space-around;font-size:14px;font-weight:700;color:#777}

.services{top:853px;font-size:14.5px;line-height:24px;color:var(--muted)}

.news{left:123px;top:975px;width:960px;height:40px;border:1px solid var(--blue);border-radius:8px;overflow:hidden}
.news-tab{position:absolute;left:0;top:0}
.news-label{position:absolute;left:17px;top:11px;color:var(--white);font-weight:700;font-size:14px}
.news-text{position:absolute;left:164px;top:10px;font-size:13px;color:var(--text)}

.copyright{left:119px;top:1058px;font-size:12px;color:var(--text)}
.foot-nav{left:530px;top:1058px;display:flex;gap:30px;font-size:12.5px;color:var(--blue)}
</style>
</head>
<body>

<header>
  <div class="abs brand"><span class="brand-dot"></span><span>47VORA</span></div>
  <nav class="abs main-nav">
    <span>Company</span><span>Creative Services</span><span>Technical Services</span><span>Partners</span><span>Contact Us</span>
  </nav>
  <address class="abs contact" style="font-style:normal">
    2715 Harlow St, Ste 804<br>
    San Francisco, CA 94107<br>
    <span class="link">415-555-0147</span><br>
    <span class="link">info@47vora-example.com</span>
  </address>
</header>

<section class="abs hero" role="img" aria-label="Grayscale photograph of the San Francisco skyline"></section>
<div class="abs slide-tab" style="left:118px"></div>
<div class="abs slide-tab" style="left:1059px"></div>
<section class="abs slide">
  <div class="slide-photo" role="img" aria-label="Motion-blurred photograph of a sprinter on a green track"></div>
  <h1 class="abs slide-title">Flexible</h1>
  <p class="abs slide-sub">The world moves too fast<br>for rigid solutions.</p>
  <div class="abs dots"><i class="on"></i><i></i><i></i><i></i><i></i><i></i></div>
</section>
<svg class="abs arrow" style="left:124px" width="32" height="52" viewBox="0 0 32 52"><path d="M28 2 L6 26 L28 50" fill="none" stroke="#fff" stroke-width="7"/></svg>
<svg class="abs arrow" style="left:1044px" width="32" height="52" viewBox="0 0 32 52"><path d="M4 2 L26 26 L4 50" fill="none" stroke="#fff" stroke-width="7"/></svg>

<section>
  <article class="abs card" style="left:126px">
    <div class="card-head">Creative Services</div>
    <div class="card-art" role="img" aria-label="Colourful abstract flower illustration" style="background:radial-gradient(ellipse at 50% 100%,#e040a0 0%,#6a6ae0 35%,#40c8a0 55%,#fff 75%)"></div>
    <svg class="card-corner" width="40" height="40" viewBox="0 0 40 40"><path d="M40 0 V40 H0 Z" fill="var(--blue)"/><path d="M24 27 H36 M30 21 V33" stroke="#fff" stroke-width="2.5"/></svg>
  </article>
  <article class="abs card" style="left:452px">
    <div class="card-head">Business &amp; Technical Services</div>
    <div class="card-art" role="img" aria-label="Photograph of interlocking metal gears" style="background:radial-gradient(ellipse at 50% 70%,#666 0%,#aaa 40%,#fff 72%)"></div>
    <svg class="card-corner" width="40" height="40" viewBox="0 0 40 40"><path d="M40 0 V40 H0 Z" fill="var(--blue)"/><path d="M24 27 H36 M30 21 V33" stroke="#fff" stroke-width="2.5"/></svg>
  </article>
  <article class="abs card" style="left:776px">
    <div class="card-head">Partners</div>
    <div class="card-art" role="img" aria-label="Glossy blue globe" style="background:radial-gradient(circle at 50% 52%,#7fd0f0 0%,#2a95c8 30%,#fff 46%)"></div>
    <svg class="card-corner" width="40" height="40" viewBox="0 0 40 40"><path d="M40 0 V40 H0 Z" fill="var(--blue)"/><path d="M24 27 H36 M30 21 V33" stroke="#fff" stroke-width="2.5"/></svg>
  </article>
</section>

<div class="abs rule" style="top:753px"></div>
<h2 class="abs featured">Featured<br>Clients</h2>
<svg class="abs" style="left:222px;top:772px" width="22" height="38" viewBox="0 0 22 38"><path d="M3 2 L18 19 L3 36" fill="none" stroke="var(--blue)" stroke-width="5"/></svg>
<div class="abs clients">
  <span>Ardenne</span><span>Pellmore</span><span>Kovix</span><span>Halvern</span><span>Orrin</span><span>Tavelo</span><span>Quorra</span><span>Brisk Field</span><span>Lumasip</span>
</div>
<div class="abs rule" style="top:825px"></div>

<ul class="abs services" style="left:128px;top:851px;list-style:none">
  <li>Application Software and Web Development</li>
  <li>Business Process Re-Design (BPR)</li>
  <li>Systems Analysis and Requirement Docs</li>
  <li>Mentoring and Training</li>
</ul>
<ul class="abs services" style="left:452px;top:849px;list-style:none">
  <li>Network/Hardware Installation Services</li>
  <li>System Design and Architecture</li>
  <li>Vendor Management</li>
  <li>Docuvault Architecture and Implementation</li>
</ul>
<ul class="abs services" style="left:776px;top:844px;list-style:none">
  <li>Print &amp; Package Design</li>
  <li>Brand and Identity Creation</li>
  <li>Website and User Experience Design</li>
  <li>Illustration Design</li>
</ul>

<section class="abs news">
  <svg class="news-tab" width="140" height="40" viewBox="0 0 140 40"><path d="M0 0 H124 L137 20 L124 40 H0 Z" fill="var(--blue)"/></svg>
  <span class="news-label">Latest News</span>
  <span class="news-text">Updated news item for the day goes here</span>
</section>

<div class="abs rule" style="top:1040px"></div>
<footer>
  <p class="abs copyright">Copyright 2011, 47Vora, LLC All rights reserved.</p>
  <nav class="abs foot-nav">
    <span>Home</span><span>Company</span><span>Technical Services</span><span>Creative Services</span><span>Partners</span><span>Contact Us</span>
  </nav>
</footer>

</body>
</html>
```